Seeking funky, innovative business cards

I am looking to refresh our current business cards to something more engaging, visual and impactful. We are a management consultancy firm, see website (www.larkstone-partners.com.au). I've included our colour scheme, sample of the slides we use and our old business cards. We would like our cards to have icons. The card should display:- Name- Title- Mobile number- Address- Email address- Website - Company logo- Our purpose statement "We create the best places on earth to work"

Contact Information for Business Card

Brennan Ulfsson
Consultant
0468 927 341
Level 3, 218 Wexley Street, Melbourne 3000
brennan@larkstone-partners.com.au
www.larkstone-partners.com.au

Purpose statement "we create the best places on earth to work"
LOGO available in google images

Font styles to use
Other font styles liked:
• Open Sans Light, Bebas Neue (open to other cool foints)

Colors
ffc214
5c5c5c
f5f5f5
fefefe

Requirements
Must have
• - Name
• - Title
• - Mobile number
• - Address
• - Email address
• - Website
• - Company logo
• - Our purpose statement "We create the best places on earth to work"
Nice to have
• - Icons
• - Colour (see our colour scheme"

```html
<!DOCTYPE html>
<html lang="en">
<head>
<meta charset="utf-8">
<title>Larkstone Partners – Business Card</title>
<link rel="stylesheet" href="https://fonts.googleapis.com/css2?family=Lato:wght@400&family=Open+Sans:wdth,wght@75..100,300..700&display=swap">
<style>
  :root {
    --page-bg: #e4e4e4;
    --yellow-light: #ffd21a;
    --yellow: #ffc214;
    --orange: #fbad2a;
    --ink: #3f4247;
    --grey: #5c5c5c;
    --grey-soft: #8a8a8a;
    --card-white: #fefefe;
    --white: #ffffff;
  }
  * { box-sizing: border-box; margin: 0; padding: 0; }
  html, body {
    width: 1200px; height: 1200px; overflow: hidden;
    background: var(--page-bg);
  }
  .card {
    position: absolute; left: 226px;
    width: 780px; height: 452px;
  }
  /* Front */
  .card-front {
    top: 106px;
    background: linear-gradient(45deg, var(--yellow-light) 0%, var(--yellow) 45%, var(--orange) 100%);
  }
  .brand {
    position: absolute; display: flex; flex-direction: column; align-items: flex-end;
    font-family: "Open Sans", sans-serif; font-weight: 300;
  }
  .brand-name { font-size: 64px; line-height: 1; letter-spacing: -1px; display: flex; align-items: center; gap: 12px; }
  .brand-dot { width: 14px; height: 14px; border-radius: 50%; flex: none; }
  .brand-sub { font-size: 13px; letter-spacing: 4px; margin-top: 4px; }
  .card-front .brand { left: 0; right: 0; top: 170px; align-items: center; color: var(--white); }
  .card-front .brand-dot { background: var(--white); }
  .card-front .brand-sub { padding-left: 150px; }
  .purpose {
    position: absolute; left: 0; right: 0; top: 270px; text-align: center;
    font-family: "Open Sans", sans-serif; font-weight: 600; font-stretch: 80%;
    font-size: 22px; color: var(--ink); text-transform: uppercase;
  }
  /* Back */
  .card-back { top: 638px; background: var(--card-white); }
  .card-back .brand { left: 110px; top: 190px; color: var(--ink); }
  .card-back .brand-dot { background: var(--yellow); }
  .contact { position: absolute; left: 416px; top: 104px; font-family: "Lato", sans-serif; }
  .contact-name { font-size: 28px; color: var(--ink); line-height: 1.2; }
  .contact-title { font-size: 18px; color: var(--yellow); margin-top: 2px; }
  .contact-rule { width: 94px; height: 2px; background: var(--yellow); margin-top: 8px; }
  .contact-address { font-size: 18px; color: var(--grey-soft); line-height: 24px; margin-top: 14px; }
  .contact-list { list-style: none; margin-top: 20px; }
  .contact-list li {
    display: flex; align-items: center; gap: 9px;
    font-size: 18px; color: var(--grey-soft); height: 27px;
  }
  .contact-icon { width: 20px; height: 20px; flex: none; }
</style>
</head>
<body>
  <section class="card card-front" aria-label="Card front">
    <div class="brand">
      <div class="brand-name"><span class="brand-dot"></span>Larkstone</div>
      <div class="brand-sub">PARTNERS</div>
    </div>
    <p class="purpose">We create the best places on earth to work!</p>
  </section>

  <section class="card card-back" aria-label="Card back">
    <div class="brand">
      <div class="brand-name"><span class="brand-dot"></span>Larkstone</div>
      <div class="brand-sub">PARTNERS</div>
    </div>
    <div class="contact">
      <h1 class="contact-name" style="font-weight:400">Brennan Ulfsson</h1>
      <p class="contact-title">Consultant</p>
      <div class="contact-rule"></div>
      <p class="contact-address">Level 3, 218 Wexley Street<br>Melbourne 3000</p>
      <ul class="contact-list">
        <li>
          <svg class="contact-icon" viewBox="0 0 20 20" aria-hidden="true">
            <circle cx="10" cy="10" r="10" fill="#fbad2a"/>
            <path d="M7 5.5l2 2.3-1 1.2c.6 1.3 1.6 2.3 2.9 2.9l1.2-1 2.3 2-1 1.6c-3.6-.3-6.7-3.4-7-7z" fill="#fff"/>
          </svg>
          0468 927 341
        </li>
        <li>
          <svg class="contact-icon" viewBox="0 0 20 20" aria-hidden="true">
            <circle cx="10" cy="10" r="10" fill="#fbad2a"/>
            <rect x="5" y="6.5" width="10" height="7" fill="#fff"/>
            <path d="M5 6.5l5 4 5-4" fill="none" stroke="#fbad2a" stroke-width="1"/>
          </svg>
          brennan@larkstone-partners.com.au
        </li>
        <li>
          <svg class="contact-icon" viewBox="0 0 20 20" aria-hidden="true">
            <circle cx="10" cy="10" r="10" fill="#fbad2a"/>
            <g fill="none" stroke="#fff" stroke-width="1">
              <circle cx="10" cy="10" r="5"/>
              <ellipse cx="10" cy="10" rx="2.2" ry="5"/>
              <path d="M5 10h10"/>
            </g>
          </svg>
          www.larkstone-partners.com.au
        </li>
      </ul>
    </div>
  </section>
</body>
</html>
```